Thornvale Group needs a business card design

We need a new business card design using the logo recently selected in a logo competition on Pixel Bazaar. Our business is a consultancy specializing in aviation and energy and the winning business card design will promote an image of precision and professionalism with creativity.

Please use the logo with the name on the front of the card and use a complementary font. Make the back white with either the light grey or dark grey logo.

Target Market(s)

Senior finance and legal leaders at aviation and energy companies

Industry/Entity Type

Management Consulting

Contact Information for Business Card

Peter Castrell
President
Thornvale Group

www.thornvalegroup.example

(555) 204-6391
pc@thornvalegroup.example

Requirements
Must have
• Professional font that goes well with the logo font

```html
<!DOCTYPE html>
<html lang="en">
<head>
<meta charset="utf-8">
<title>Thornvale Group – Business Card</title>
<link rel="stylesheet" href="https://fonts.googleapis.com/css2?family=Libre+Franklin:wght@300;400;500&family=Montserrat:wght@400&display=swap">
<style>
  :root {
    --page-bg: #e9e7e4;
    --card-face: #f3f3f2;
    --navy-deep: #0c1630;
    --navy-mid: #1b2a4c;
    --steel: #8d93a0;
    --gold: #d4c19a;
    --silver: #d9dce2;
    --brand-navy: #1d2b4d;
  }
  * { margin: 0; padding: 0; box-sizing: border-box; }
  html, body {
    width: 1200px;
    height: 969px;
    overflow: hidden;
    background: var(--page-bg);
  }
  .canvas {
    position: relative;
    width: 1200px;
    height: 969px;
  }
  .card {
    position: absolute;
    left: 100px;
    top: 200px;
    width: 1000px;
    height: 568px;
    background: var(--card-face);
    box-shadow: 0 10px 30px rgba(0,0,0,0.12);
    overflow: hidden;
  }
  .card-shapes {
    position: absolute;
    inset: 0;
  }
  .brand {
    position: absolute;
    left: 40px;
    width: 420px;
    top: 215px;
    display: flex;
    align-items: center;
    justify-content: center;
    gap: 16px;
  }
  .brand-square {
    width: 22px;
    height: 22px;
    background: var(--brand-navy);
  }
  .brand-name {
    font-family: "Montserrat", sans-serif;
    font-weight: 400;
    font-size: 38px;
    letter-spacing: 3px;
    color: var(--brand-navy);
    text-transform: uppercase;
    white-space: nowrap;
  }
  .details {
    position: absolute;
    right: 44px;
    top: 58px;
    text-align: right;
    font-family: "Libre Franklin", sans-serif;
  }
  .person-name {
    font-size: 36px;
    font-weight: 500;
    color: var(--gold);
    line-height: 42px;
  }
  .person-title {
    font-size: 28px;
    font-weight: 300;
    color: #ffffff;
    line-height: 38px;
  }
  .company {
    margin-top: 112px;
    font-size: 26px;
    font-weight: 300;
    color: #e6e8ee;
    line-height: 37px;
  }
  .contact {
    list-style: none;
    margin-top: 14px;
    font-size: 26px;
    font-weight: 300;
    color: var(--gold);
    line-height: 38px;
  }
  .contact li {
    display: flex;
    justify-content: flex-end;
    align-items: center;
    gap: 12px;
  }
  .contact svg { width: 24px; height: 24px; flex: none; }
</style>
</head>
<body>
<main class="canvas">
  <section class="card" aria-label="Thornvale Group business card">
    <svg class="card-shapes" viewBox="0 0 1000 568" width="1000" height="568" aria-hidden="true">
      <defs>
        <linearGradient id="navyPanel" x1="0" y1="0" x2="1" y2="1">
          <stop offset="0" stop-color="#233661"/>
          <stop offset="0.55" stop-color="#121e3d"/>
          <stop offset="1" stop-color="#0a1228"/>
        </linearGradient>
        <linearGradient id="silverEdge" x1="0" y1="0" x2="0" y2="1">
          <stop offset="0" stop-color="#c7ccd6"/>
          <stop offset="0.5" stop-color="#6f7584"/>
          <stop offset="1" stop-color="#2f3440"/>
        </linearGradient>
      </defs>
      <polygon points="626,0 642,0 340,568 298,568" fill="url(#silverEdge)"/>
      <polygon points="642,0 1000,0 1000,568 340,568" fill="url(#navyPanel)"/>
      <polygon points="642,0 650,0 350,568 340,568" fill="#5b6478" opacity="0.7"/>
    </svg>

    <div class="brand">
      <span class="brand-square"></span>
      <span class="brand-name">Thornvale Group</span>
    </div>

    <div class="details">
      <p class="person-name">Peter J. Castrell</p>
      <p class="person-title">President</p>
      <div class="company">
        <p>Thornvale Group LLC</p>
        <p>Finance and Strategy Consulting</p>
        <p>Aviation - Manufacturing - Energy</p>
      </div>
      <ul class="contact">
        <li>(555) 204-6391
          <svg viewBox="0 0 24 24" aria-label="phone"><path fill="#e6e8ee" d="M3 8c0-2 2-3 9-3s9 1 9 3v2h-5V8.5c-1-.4-2.4-.5-4-.5s-3 .1-4 .5V10H3zM7 11l2-2h6l2 2 3 3v5H4v-5zm5 1.5a2.5 2.5 0 1 0 0 5 2.5 2.5 0 0 0 0-5z"/></svg>
        </li>
        <li>pc@thornvalegroup.example
          <svg viewBox="0 0 24 24" aria-label="email"><path fill="#e6e8ee" d="M3 6h18v12H3z"/><path fill="none" stroke="#1b2a4c" stroke-width="1.6" d="M3.5 6.5l8.5 7 8.5-7"/></svg>
        </li>
        <li>thornvalegroup.example
          <svg viewBox="0 0 24 24" aria-label="website"><circle cx="12" cy="12" r="9" fill="#e6e8ee"/><path fill="none" stroke="#1b2a4c" stroke-width="1.4" d="M3 12h18M12 3c3 3 3 15 0 18M12 3c-3 3-3 15 0 18"/></svg>
        </li>
      </ul>
    </div>
  </section>
</main>
</body>
</html>
```